Elegant Business Card for Technology Company

Client is a supplier of innovative industrial communications and automation equipment since 2002. This contest is to gather fresh ideas for a redesign of the existing business card. Client is looking for design that best communicates tagline "Industrial Networking and Computing Specialist".

Design submissions should look modern, clean, elegant and professional. It should not be cluttered. Use white as the primary colour. Orange and black as secondary colour. Refer to jpeg File 1 on the current design.

Fonts used by Client used include Arial Regular, Arial Black, Roboto Regular, Roboto Black and Lato.

The winning design will be sent for offset printing using super white 250gsm artcard paper (open for suggestions).

Target Market(s)

System Engineers, Project Managers, Purchasing Managers from companies providing engineering services for Smart Cities.

Industry/Entity Type

Information Technology

Contact Information for Business Card

Refer to PDF File 3 for Business Card Details. Priority of short contact information would be as follows Name > Job Title > Email > Mobile > Web > Tel > Fax > Business Address >UEN (UEN represents company registration number)

Font styles to use
Sans Serif

Colors
ffffff
f37122
000000
5c5c5c

Requirements
Must have
• Refer to AI File 2 (Company Logo) & PDF File 3 (Information on Namecard)
Should not have
• No QR codes
• No Social Media Icons
• Do not create full Black or Orange colour background

```html
<!DOCTYPE html>
<html lang="en">
<head>
<meta charset="utf-8">
<title>Voltrix Business Card</title>
<link href="https://fonts.googleapis.com/css2?family=Roboto:wght@400;500;900&display=swap" rel="stylesheet">
<style>
  :root {
    --white: #ffffff;
    --orange: #f37122;
    --black: #000000;
    --grey: #5c5c5c;
    --rule: #bdbdbd;
    --stage: #e6e6e6;
  }
  * { box-sizing: border-box; margin: 0; padding: 0; }
  html, body { width: 1200px; height: 900px; overflow: hidden; }
  body {
    background: var(--stage);
    font-family: "Roboto", Arial, sans-serif;
    position: relative;
  }
  .card {
    position: absolute;
    width: 700px;
    height: 400px;
    border-radius: 28px;
    overflow: hidden;
    box-shadow: 0 12px 30px rgba(0,0,0,.25);
  }
  .card-front { left: 90px; top: 30px; background: var(--orange); }
  .card-back { left: 410px; top: 470px; background: var(--white); }
  .card svg.band { position: absolute; inset: 0; width: 700px; height: 400px; }

  .brand { position: absolute; display: flex; align-items: center; gap: 12px; }
  .brand-dot { width: 70px; height: 70px; border-radius: 50%; flex: none; }
  .brand-name { font-weight: 900; font-size: 40px; letter-spacing: .5px; line-height: 1; color: var(--black); white-space: nowrap; }

  .card-front .brand { left: 60px; top: 135px; }
  .card-front .brand-dot { background: var(--white); }

  .services {
    position: absolute; left: 380px; top: 68px;
    list-style: none; color: var(--white);
    font-size: 15px; line-height: 1.35;
  }

  .tagline {
    font-family: "Roboto", Arial, sans-serif;
    font-size: 17px; font-weight: 500; fill: var(--white); letter-spacing: .4px;
  }

  .card-back .brand { left: 80px; top: 110px; }
  .card-back .brand-dot { background: var(--orange); }
  .company { position: absolute; left: 80px; top: 198px; }
  .company-name { font-size: 16px; font-weight: 500; color: var(--black); }
  .company-uen { font-size: 15px; color: var(--orange); margin-top: 4px; }
  .company-uen span { color: var(--black); }

  .divider {
    position: absolute; left: 410px; top: 40px;
    width: 1px; height: 160px; background: var(--rule);
  }
  .person { position: absolute; left: 432px; top: 42px; }
  .person-name { font-size: 22px; font-weight: 900; color: var(--black); letter-spacing: .5px; }
  .person-title { font-size: 15px; color: var(--orange); letter-spacing: .5px; margin-top: 2px; }
  .contacts { list-style: none; margin-top: 12px; }
  .contacts li {
    display: flex; align-items: center; gap: 10px;
    font-size: 14.5px; color: var(--black); line-height: 22px;
  }
  .contacts svg { width: 13px; height: 13px; flex: none; }
  .address { font-size: 16px; fill: var(--white); letter-spacing: .3px; font-family: "Roboto", Arial, sans-serif; }
</style>
</head>
<body>

<section class="card card-front">
  <svg class="band" viewBox="0 0 700 400" aria-hidden="true">
    <defs>
      <path id="front-curve" d="M80 380 Q420 340 690 215"/>
    </defs>
    <path d="M0 340 Q380 310 700 190 L700 400 L0 400 Z" fill="var(--white)"/>
    <path d="M0 348 Q380 318 700 200 L700 400 L0 400 Z" fill="var(--black)"/>
    <text class="tagline"><textPath href="#front-curve">INDUSTRIAL NETWORKING AND COMPUTING SPECIALIST</textPath></text>
  </svg>
  <div class="brand">
    <span class="brand-dot"></span>
    <span class="brand-name">VOLTRIX</span>
  </div>
  <ul class="services">
    <li>Industrial Ethernet / Wireless / Cellular</li>
    <li>Industrial and Embedded Computing</li>
    <li>Serial / Fieldbus Connectivity</li>
    <li>IP Video Surveillance</li>
    <li>Remote Automation</li>
  </ul>
</section>

<section class="card card-back">
  <svg class="band" viewBox="0 0 700 400" aria-hidden="true">
    <defs>
      <path id="back-curve" d="M360 355 Q540 315 690 255"/>
      <path id="back-curve-2" d="M385 378 Q560 338 695 280"/>
    </defs>
    <path d="M0 355 Q400 330 700 220 L700 400 L0 400 Z" fill="var(--orange)"/>
    <path d="M0 362 Q400 338 700 230 L700 400 L0 400 Z" fill="var(--black)"/>
    <text class="address"><textPath href="#back-curve">25 Kallang Way Tech Hub #02-18</textPath></text>
    <text class="address"><textPath href="#back-curve-2">(Lobby B), Singapore 349123</textPath></text>
  </svg>

  <div class="brand">
    <span class="brand-dot"></span>
    <span class="brand-name">VOLTRIX</span>
  </div>
  <div class="company">
    <p class="company-name">VOLTRIX ASIA PACIFIC PTE LTD</p>
    <p class="company-uen">UEN No: <span>200301457K</span></p>
  </div>

  <div class="divider"></div>

  <div class="person">
    <p class="person-name">DANIEL LOH</p>
    <p class="person-title">SALES MANAGER</p>
    <ul class="contacts">
      <li>
        <svg viewBox="0 0 12 12"><rect x="3" y="0.5" width="6" height="11" rx="1.2" fill="none" stroke="var(--orange)" stroke-width="1.3"/><circle cx="6" cy="9.5" r=".8" fill="var(--orange)"/></svg>
        +65 8123 4567
      </li>
      <li>
        <svg viewBox="0 0 12 12"><path d="M2.5 1 L4.5 1 L5.3 3.5 L4 4.6 Q5 7 7.4 8 L8.5 6.7 L11 7.5 L11 9.5 Q10.5 11 9 11 Q1 10 1 3 Q1 1.5 2.5 1 Z" fill="var(--orange)"/></svg>
        +65 6555 1020
      </li>
      <li>
        <svg viewBox="0 0 12 12"><rect x="3" y="1" width="6" height="3.5" fill="none" stroke="var(--orange)" stroke-width="1.2"/><rect x="1" y="4.5" width="10" height="4.5" rx="1" fill="var(--orange)"/><rect x="3" y="8" width="6" height="3" fill="none" stroke="var(--orange)" stroke-width="1.2"/></svg>
        +65 6555 1031
      </li>
      <li>
        <svg viewBox="0 0 12 12"><rect x="0.8" y="2.3" width="10.4" height="7.4" fill="none" stroke="var(--orange)" stroke-width="1.3"/><path d="M1 2.6 L6 6.5 L11 2.6" fill="none" stroke="var(--orange)" stroke-width="1.2"/></svg>
        sales@voltrix.example
      </li>
      <li>
        <svg viewBox="0 0 12 12"><circle cx="6" cy="6" r="5" fill="none" stroke="var(--orange)" stroke-width="1.2"/><ellipse cx="6" cy="6" rx="2.2" ry="5" fill="none" stroke="var(--orange)" stroke-width="1"/><path d="M1 6 H11" stroke="var(--orange)" stroke-width="1"/></svg>
        www.voltrix.example
      </li>
    </ul>
  </div>
</section>

</body>
</html>
```